Electrician Business Card/ company logo/small business

New Business Cards and logo needed that will catch peoples eye and say we went that extra step. Attached is a design possibly to be incorporated, if u have your own great, lets see it!... This will be a small local business. thank you for all you do!
Halvern Electric
Ned Fosky Owner
Journeyman Electrician
phone 1.555.208.3471
email: KQLHalvernElectric@quellmail.net
call for free estimate!
Updates

Accepted and approved for cards

Target Market(s)

support small local business

Industry/Entity Type

Electrical,

Contact Information for Business Card

name, title,company/ logo, phone, email, free estimate

Other font styles liked:
• easy to read

Colors

Designer to choose colors to be used in the design.

Requirements
Must have
• eye catching everything! logo and halvern electric listed on business card/logo, incorp logo in the background of card
Nice to have
• lightening bolts in eyes or around the triangle? vertical, modern, any design that would be unique and stand out
Should not have
• pinks, reds, yellows,brown

```html
<!DOCTYPE html>
<html lang="en">
<head>
<meta charset="utf-8">
<title>Halvern Electric – Business Cards</title>
<link rel="stylesheet" href="https://fonts.googleapis.com/css2?family=Archivo:wght@800&family=Arimo:wght@400&display=swap">
<style>
  :root {
    --backdrop: #2a2a2c;
    --card: #0b0b0c;
    --card-edge: #1a1a1b;
    --brand-blue: #1a8be0;
    --text-light: #d9d9d9;
    --divider: #3a3a3c;
  }
  * { margin: 0; padding: 0; box-sizing: border-box; }
  html, body { width: 1200px; height: 900px; overflow: hidden; }
  body {
    background: var(--backdrop);
    font-family: "Arimo", Arial, sans-serif;
    display: flex;
    flex-direction: column;
    align-items: center;
    justify-content: center;
    gap: 44px;
  }
  .card {
    width: 640px;
    height: 366px;
    background: var(--card);
    border: 1px solid var(--card-edge);
    position: relative;
  }
  /* Front side */
  .card--front { display: flex; align-items: center; }
  .front__brand {
    width: 250px;
    height: 100%;
    display: flex;
    flex-direction: column;
    align-items: center;
    justify-content: center;
    gap: 14px;
  }
  .brand-mark {
    width: 22px; height: 22px;
    background: var(--brand-blue);
  }
  .wordmark {
    font-family: "Archivo", "Arial Black", sans-serif;
    font-weight: 800;
    color: var(--brand-blue);
    text-transform: uppercase;
    letter-spacing: 0.02em;
    line-height: 1.05;
    text-align: center;
  }
  .front__brand .wordmark { font-size: 26px; }
  .front__divider {
    width: 1px; height: 200px;
    background: var(--divider);
  }
  .front__details { padding-left: 38px; }
  .person__name {
    font-family: "Archivo", "Arial Black", sans-serif;
    font-weight: 800;
    font-size: 28px;
    color: var(--brand-blue);
    text-transform: uppercase;
    line-height: 1;
  }
  .person__title {
    font-size: 15px;
    color: var(--text-light);
    margin-top: 4px;
  }
  .contact { list-style: none; margin-top: 26px; }
  .contact__item {
    display: flex; align-items: center; gap: 9px;
    font-size: 15px; color: var(--text-light);
    margin-bottom: 7px;
  }
  .contact__icon { width: 14px; height: 14px; flex: none; }
  /* Back side */
  .card--back {
    display: flex; align-items: center; justify-content: center; gap: 16px;
  }
  .card--back .brand-mark { width: 30px; height: 30px; }
  .card--back .wordmark { font-size: 40px; text-align: left; }
</style>
</head>
<body>
  <section class="card card--front" aria-label="Business card front">
    <div class="front__brand">
      <span class="brand-mark"></span>
      <div class="wordmark">Halvern<br>Electric</div>
    </div>
    <div class="front__divider"></div>
    <div class="front__details">
      <h1 class="person__name">Ned Fosky</h1>
      <p class="person__title">Journeyman Electrician</p>
      <ul class="contact">
        <li class="contact__item">
          <svg class="contact__icon" viewBox="0 0 24 24" aria-hidden="true"><path fill="#1a8be0" d="M6.6 10.8a15.1 15.1 0 0 0 6.6 6.6l2.2-2.2a1 1 0 0 1 1-.25 11.4 11.4 0 0 0 3.6.57 1 1 0 0 1 1 1V20a1 1 0 0 1-1 1A17 17 0 0 1 3 4a1 1 0 0 1 1-1h3.5a1 1 0 0 1 1 1c0 1.25.2 2.45.57 3.57a1 1 0 0 1-.25 1z"/></svg>
          1.555.208.3471
        </li>
        <li class="contact__item">
          <svg class="contact__icon" viewBox="0 0 24 24" aria-hidden="true"><path fill="#1a8be0" d="M2 5h20v14H2z"/><path fill="none" stroke="#0b0b0c" stroke-width="1.8" d="M2.5 5.5 12 13l9.5-7.5"/></svg>
          KQLHalvernElectric@quellmail.net
        </li>
      </ul>
    </div>
  </section>

  <section class="card card--back" aria-label="Business card back">
    <span class="brand-mark"></span>
    <div class="wordmark">Halvern<br>Electric</div>
  </section>
</body>
</html>
```